Business Card for a Dental Office

The design should communicate integrity, quality and reliability. We also want the card look elegant, simple, but still stand out, different from the traditional-dental-office business card.

Industry/Entity Type

Business

```html
<!DOCTYPE html>
<html lang="en">
<head>
<meta charset="utf-8">
<title>Marlow Dental Care – Business Card</title>
<link rel="stylesheet" href="https://fonts.googleapis.com/css2?family=Lato:wght@400;700&display=swap">
<style>
  :root {
    --backdrop: #e9e7e4;
    --card: #ffffff;
    --ink: #141414;
    --gold-text: #9c820c;
    --band-edge: #c7ae05;
    --band-mid: #f6ec22;
    --rule: #a8930c;
    --shadow: rgba(0,0,0,0.18);
  }
  * { margin: 0; padding: 0; box-sizing: border-box; }
  html, body { width: 1200px; height: 900px; overflow: hidden; }
  body { background: var(--backdrop); position: relative; font-family: "Lato", sans-serif; color: var(--ink); }

  .card { position: absolute; background: var(--card); box-shadow: 0 6px 18px var(--shadow); overflow: hidden; }
  .gold-band { position: absolute; left: 0; right: 0;
    background: linear-gradient(180deg, var(--band-edge) 0%, var(--band-mid) 45%, var(--band-mid) 60%, var(--band-edge) 100%); }

  .brand-name { font-family: "Lato", sans-serif; font-weight: 700; line-height: 1; color: var(--ink); white-space: nowrap; }
  .brand-tagline { font-family: "Lato", sans-serif; font-weight: 700; letter-spacing: 0.4px; white-space: nowrap; }

  /* Front */
  .card-front { left: 77px; top: 34px; width: 589px; height: 364px; }
  .front-brand { position: absolute; left: 34px; top: 84px; }
  .card-front .brand-name { font-size: 34px; }
  .card-front .brand-tagline { font-size: 15px; color: var(--gold-text); margin-top: 8px; }
  .card-front .gold-band { top: 171px; bottom: 0; }
  .holder { position: absolute; left: 31px; top: 20px; }
  .holder-name { font-weight: 700; font-size: 19.5px; }
  .holder-role { font-size: 15px; margin-top: 3px; }
  .contact-list { position: absolute; left: 0; top: 84px; width: 248px; list-style: none; }
  .contact-item { display: flex; align-items: center; height: 32px; padding-left: 34px; font-size: 15px; }
  .contact-item + .contact-item { border-top: 1px solid var(--rule); }
  .contact-item svg { width: 12px; height: 12px; margin-right: 12px; flex: none; }

  /* Back */
  .card-back { left: 388px; top: 505px; width: 567px; height: 352px; }
  .card-back .gold-band { top: 110px; height: 131px; display: flex; flex-direction: column; align-items: center; justify-content: center; }
  .card-back .brand-name { font-size: 40px; }
  .card-back .brand-tagline { color: var(--ink); font-size: 19px; margin-top: 10px; }
</style>
</head>
<body>
  <section class="card card-front">
    <div class="front-brand">
      <div class="brand-name">Marlow Dental Care</div>
      <div class="brand-tagline">A healthy smile lasts a lifetime</div>
    </div>
    <div class="gold-band">
      <div class="holder">
        <div class="holder-name">Daniel Hart</div>
        <div class="holder-role">Managing Director</div>
      </div>
      <ul class="contact-list">
        <li class="contact-item">
          <svg viewBox="0 0 12 12" aria-hidden="true"><path d="M2.5 0.8 L4.3 2.9 L3.4 4.2 Q4.6 6.9 7.8 8.6 L9.1 7.7 L11.2 9.5 L9.9 11.2 Q5.6 11 2.6 7.5 Q0.6 5 0.9 2 Z" fill="#141414"/></svg>
          044-555 010 203
        </li>
        <li class="contact-item">
          <svg viewBox="0 0 12 12" aria-hidden="true"><rect x="0.5" y="2" width="11" height="8" fill="#141414"/><path d="M1 2.6 L6 6.4 L11 2.6" stroke="#f6ec22" stroke-width="1" fill="none"/></svg>
          info@marlowdental.com
        </li>
        <li class="contact-item">
          <svg viewBox="0 0 12 12" aria-hidden="true"><g fill="none" stroke="#141414" stroke-width="1.5"><rect x="0.8" y="5" width="6" height="3.2" rx="1.6" transform="rotate(-45 3.8 6.6)"/><rect x="5.2" y="3.8" width="6" height="3.2" rx="1.6" transform="rotate(-45 8.2 5.4)"/></g></svg>
          www.marlowdental.com
        </li>
      </ul>
    </div>
  </section>

  <section class="card card-back">
    <div class="gold-band">
      <div class="brand-name">Marlow Dental Care</div>
      <div class="brand-tagline">A healthy smile lasts a lifetime</div>
    </div>
  </section>
</body>
</html>
```